Etiketten-Design für einen importierten Honig
Zielgruppe
Wir importieren originalen Manuka Honig aus Neuseeland. Der Manuka Honig ist bekannt für seine besonderen Eigenschaften (antibakteriell, etc.). Ein Glas unseres Honigs (500g) kostet zwischen 30 und 150 EUR.
Unsere Zielgruppe sind gesundheitsbewusste Kunden, die wenig preissensibel sind. Überwiegend wird der Manuka Honig im Fachhandel (z.B. Reformhaus, Drogerie, Biomarkt, etc.) verkauft. Der Großteil unserer Kunden ist 30+ Jahre.
Aufgabenstellung
Bei dem Etikett handelt es sich um das erste Produktetikett. Damit ist in der Farbgestaltung noch alles offen. Das Logo und der Name ist jedoch fix.
Das Etikett ist wird auf einem bpa-freien schwarzen Plastikbehälter angebracht. Dieser ist bei Manuka Honigen Standard aufgrund des langen Transports von Neuseeland nach Deutschland (gerne googeln). Der Deckel dieses Behälters ist schwarz.
Nachdem es sich um ein hochpreisiges Produkt handelt, soll das Etikett diese hohe Wertigkeit widerspiegeln. Damit ist eine Veredelung des Etiketts notwendig. Viele Konkurrenten arbeiten mit Gold, alternative Farben sind jedoch auch möglich.
Das Etikett überdeckt drei der vier Seiten des Plastikbehälters (vorne + links + rechts). Die Maße sind 160 mm x 60 mm. Zusätzlich zu den Etikettenmaßen bitte 2 mm Beschnittzugabe je Seite hinzufügen.
Hintergrundinformationen zu unserer Marke:
- Der Markenname lautet Kalvio. Der Markenname leitet sich von der ersten Imkerin Neuseelands ab - Edith Carrow. Sie hatte im Jahr 1839 die ersten Bienenstöcke nach Neuseeland gebracht und den ersten Manuka Honig geerntet.
- Unser Logo ist eine Verbindung einer Frau und den neuseeländischen Farn. Dieses Logo stellt also direkt eine Verbindung zu Neuseeland dar.
- Unsere Marke Kalvio ist eine qualitativ hochwertige, luxuriöse und hochpreisige Marke. Genau wie in dem Logo selbst, sollen diese Verbindungen zu Neuseeland, der Natur (Honig ist ein Naturprodukt) und Edith Carrow auch auf dem Etikett zu finden sein.
Wonach suchen wir:
- Wir sind auf der Suche nach einem einzigartigen Design, der unseren Honig besonders hervorhebt. Das Etikett soll auffällig sein und uns von anderen unterscheiden. (Eye-catching)
- Eine Veredelung des Etiketts ist Pflicht, da dies für uns die Wertigkeit des Etiketts und des Produktes stark erhöht. In welcher Art die Veredelung durchgeführt wird, ist Ihnen überlassen.
Das dürfen Sie frei wählen:
- Bisher haben..

```html
<!DOCTYPE html>
<html lang="de">
<head>
<meta charset="utf-8">
<title>Kalvio Manuka Honig – Etikett</title>
<link rel="stylesheet" href="https://fonts.googleapis.com/css2?family=Montserrat:wght@300;400;600&family=Cormorant+Garamond:wght@500&display=swap">
<style>
  :root {
    --page: #d9d9d9;
    --label: #0c0c0c;
    --gold: #c9a35b;
    --gold-soft: rgba(201, 163, 91, .55);
    --gold-fade: rgba(201, 163, 91, .12);
    --white: #ffffff;
    --blob: #4a4a4a;
  }
  * { margin: 0; padding: 0; box-sizing: border-box; }
  html, body { width: 1200px; height: 1200px; overflow: hidden; background: var(--page); }
  .label {
    position: absolute; left: 100px; top: 160px;
    width: 1000px; height: 880px;
    background: var(--label);
    overflow: hidden;
    font-family: "Montserrat", sans-serif;
    color: var(--white);
  }
  .floral {
    position: absolute;
    background: radial-gradient(ellipse at 50% 50%, var(--blob) 0%, #2a2a2a 70%, transparent 100%);
    border-radius: 45% 55% 50% 40%;
    opacity: .85;
  }
  .floral--left { left: 34px; top: 54px; width: 241px; height: 454px; }
  .floral--right { left: 641px; top: 3px; width: 337px; height: 344px; }
  .floral--bottom { left: 692px; top: 672px; width: 300px; height: 208px; border-radius: 55% 45% 0 0; }

  .brand-frame {
    position: absolute; left: 272px; top: 0; width: 460px; height: 281px;
    border: 2px solid var(--gold); border-top: none;
  }
  .brand-frame .dot {
    position: absolute; left: 50%; top: 68px; width: 86px; height: 86px;
    margin-left: -43px; border-radius: 50%; background: var(--gold);
  }
  .brand-name {
    position: absolute; left: 0; right: 0; top: 200px;
    text-align: center;
    font-family: "Cormorant Garamond", serif; font-weight: 500;
    font-size: 38px; letter-spacing: 8px; color: var(--gold);
  }

  .title { position: absolute; left: 272px; width: 456px; text-align: center; }
  .title--manuka { top: 325px; font-size: 96px; font-weight: 600; letter-spacing: 2px; line-height: 1; }
  .title--honig { top: 430px; font-size: 78px; font-weight: 300; letter-spacing: 34px; line-height: 1; padding-left: 34px; }
  .rule { position: absolute; left: 272px; width: 456px; height: 2px; background: var(--gold); }
  .rule--top { top: 534px; }
  .rule--bottom { top: 593px; }
  .origin {
    position: absolute; left: 272px; width: 456px; top: 550px; text-align: center;
    font-size: 24px; letter-spacing: 7px; font-weight: 400;
  }

  .grade { position: absolute; left: 111px; top: 596px; width: 180px; height: 198px; }
  .grade-text {
    position: absolute; left: 0; width: 180px; top: 58px; text-align: center;
    font-size: 36px; font-weight: 400; line-height: 1.1; color: var(--white);
  }

  .map {
    position: absolute; left: 483px; top: 400px; width: 490px; height: 320px;
    border-radius: 24px;
    background: radial-gradient(ellipse at 55% 50%, var(--gold-soft) 0%, var(--gold-fade) 75%, transparent 100%);
  }
  .weight {
    position: absolute; left: 729px; top: 735px;
    font-size: 30px; font-weight: 400; color: var(--white);
  }
</style>
</head>
<body>
  <main class="label">
    <div class="floral floral--left" role="img" aria-label="Line-Art Manukablüten mit grauen Flächen"></div>
    <div class="floral floral--right" role="img" aria-label="Line-Art Manukablüte mit grauen Flächen"></div>
    <div class="floral floral--bottom" role="img" aria-label="Line-Art Blatt mit grauer Fläche"></div>

    <div class="brand-frame">
      <span class="dot"></span>
      <div class="brand-name">KALVIO</div>
    </div>

    <div class="map" role="img" aria-label="Karte von Neuseeland aus goldenen Waben"></div>

    <h1 class="title title--manuka">MANUKA</h1>
    <div class="title title--honig">HONIG</div>
    <span class="rule rule--top"></span>
    <div class="origin">AUS NEUSEELAND</div>
    <span class="rule rule--bottom"></span>

    <div class="grade">
      <svg width="180" height="198" viewBox="0 0 180 198">
        <polygon points="90,6 170,52 170,146 90,192 10,146 10,52" fill="none" stroke="var(--white)" stroke-width="3"/>
        <polygon points="90,16 161,57 161,141 90,182 19,141 19,57" fill="none" stroke="var(--gold)" stroke-width="3"/>
      </svg>
      <div class="grade-text">MGO<br>450+</div>
    </div>

    <div class="weight">℮500 g</div>
  </main>
</body>
</html>
```